Website development company website

ABOUT COMPANY
Hi everyone! We're a Melbourne, Australia website development company in a need of a website design that will make online store merchants want to engage our services.
We specialise exclusively in Torvista e-commerce platform (https://torvista-platform.example/). What distinguishes our business from competition is that rather than designing and building brand new websites, we offer development, support and maintenance services to established websites. Maintenance and Support are the keywords representing our business.
Our potential clients are people with broken, slow and underperforming Torvista installations who need assistance getting their websites up and making sales. Our website must pass the message that we can help, and provide quick means of making contact.
DESIGN
Overall, we're looking for a slick, clean, airy, conservative design. No need to do anything crazy, try to stick to what's "standard" in website design these days and make it easy on all of us. The website is unlikely to be updated too often so it needs to look attractive and fresh first time over and after a year, too.
Attached is our new logo, which you'll be able to take the basic idea from, the colors and fonts. Though, don't use the fonts from the logo in the website, stick to the standard widely supported fonts. Additional use of Google fonts is fine.
Don't overdo it with colors, stick to conservative basic color set and only use the colors from the log for accents like headings etc. Please, don't be tempted to use the blue and orange as background of whole blocks, other than perhaps footer. Thanks.
For the images used, I'd like to stay away from a design studio/digital agency feel and lean more towards professional support and maintenance services. I'm thinking images of content merchants doing their job. Something along the lines of "We'll be taking care of the website so that you only need to care about the business".
Some ideas I like:
http://www.plumframe-pics.example/detail/photo/portrait-of-confident-male-design-professional-royalty-free-image/572048163
http://www.plumframe-pics.example/detail/photo/designer-taking-picture-of-hat-high-res-stock-photography/839207514
http://www.plumframe-pics.example/detail/photo/woman-packaging-pottery-royalty-free-image/216684093
Images of colorful shopping bags and shopping carts are over the top and not serious enough. Instead of images matching Online Shopping, I'd try going more for Stability, Reliability, Performance.
Our existing website is http://www.bravuln.example. Please, don't take design ideas from it, but it will give you a picture of the structure of our new website and content that's going to be used initially.
If you could include a basic icon set to use throughout the website, that would be great. If the icons could match our logo (attached), it would be a big plus.
ALL PAGES
Every page must contain clearly visible phone number (1300 648 907) and a Contact Us Now button, which opens an AJAX driven popup form with Name, Email, Phone and Message to be sent through.
To start with, main menu items will be Torvista, Portfolio, Contact.
At the bottom of each page, please, include a newsletter subscription form with text Subscribe to Torvista Support and Security Updates.
For the footer, I'd like to see a logo strip with the following logos in grayscale (no need to link anywhere): Torvista, QRX, DataVane, NCB. You'll find the logos on Google Images.
Standard footer columns follow. Here, I'd like to see logos in color: Torvista Certified Developer, Torvista Ceritified Solution Provider. Again, the logos are on Google Images.
No social media logos/links necessary anywhere on the website.
...and then the copyright line.
FRONT PAGE
Large slider with images that would appeal to our target audience. Keywords here would be Torvista System Audit, Torvista Performance Optimisation, Torvista Website Emergency Recovery, Torvista Development Infrastructure Hosting. We'll have a static page created for each of these to link to.
In a corner of the slider, or on the edge, can I have an overlay with logos in color (same as footer): Torvista Certified Developer, Torvista Ceritified Solution Provider.
Underneath, a number of blocks, each with an image and teaser that we'll use to link to various pages throughout the website.
PORTFOLIO PAGE
I'm thinking a single long page with a block per client, which will contain project name, description from us and a testimonial from client. Also, each block will contain a single large screenshot. No gallery or slideshow is necessary here, just one image per project.
I'll leave the layout up to you, but try to put yourself in the shoes of a potential client reviewing our past work by simply scrolling down this one page.
CONTACT US PAGE
Separate page with the same form as above, phone number (1300 648 907), email address (support@kavreo.example), address (Suite 42, Level 3|8 Wattlebrook Lane|Fernvale Heights VIC 3999), and a grayscale Google Map.
CODING UP
Coding up into static HTML/CSS/JS is equally important as the design itself. We're a website development company, we'll be integrating the theme. We will spot any issues and we will point them out.
Coded up design must be fully responsive. Enough said.
To be able to create any content in future, we'd like one extra page coded up with samples of all themed elements, lists, forms, buttons, 2, 3, 4-column layout, alerts, icons, etc. This page does not need to be designed, only coded up.
The design will be integrated into Drupal using Twig. If possible at all, try to keep it in mind when designing and coding up, and make the integration into a Drupal theme easier for us.
GOOD LUCK!
That's it. Let me know if anything needs clarifying. So far I've had a great experience with ArtFlockly. I don't doubt some great designs will emerge. Clever ideas are highly appreciated, but also make it clear you've read and followed the points in this brief. Cheers, Tom

```html
<!DOCTYPE html>
<html lang="en">
<head>
<meta charset="utf-8">
<title>Kavreo – Torvista eCommerce Support</title>
<link rel="stylesheet" href="https://fonts.googleapis.com/css2?family=Roboto:wght@400;500;700&family=Open+Sans:wght@400;600;700&display=swap">
<style>
:root{
  --navy:#0d3b6e;
  --orange:#e8782a;
  --text:#555a5f;
  --light:#f1f1f1;
  --card:#f6f6f6;
  --border:#dcdcdc;
  --grey-logo:#8e8e8e;
  --white:#ffffff;
}
*{margin:0;padding:0;box-sizing:border-box}
html,body{width:703px;height:1200px;overflow:hidden;background:var(--white)}
body{position:relative;font-family:"Open Sans",Arial,sans-serif;color:var(--text)}
.abs{position:absolute}

/* hero */
.hero{left:0;top:0;width:703px;height:427px;
  background:linear-gradient(100deg,#d8d2cb 0%,#e9e4de 25%,#c9b7a6 48%,#a9988a 65%,#c7c2bd 82%,#dfe2e5 100%)}
.topbar{left:0;top:0;width:703px;height:64px;background:rgba(255,255,255,.72)}
.brand{left:46px;top:19px;display:flex;align-items:center;gap:8px;
  font-family:"Roboto",Arial,sans-serif;font-weight:700;font-size:24px;color:var(--navy)}
.brand-mark{width:14px;height:14px;background:var(--orange)}
.main-nav{top:27px;left:372px;display:flex;gap:0;font-family:"Roboto",Arial,sans-serif;font-size:10px;color:#222}
.main-nav a{color:inherit;text-decoration:none;position:absolute;white-space:nowrap}
.main-nav a.active{color:var(--navy)}
.hero-title{right:49px;top:158px;text-align:right;font-family:"Roboto",Arial,sans-serif;color:var(--navy);font-weight:700}
.hero-title .line1{font-size:24.5px;letter-spacing:.2px}
.hero-title .line2{font-size:19px;font-weight:500;margin-top:3px}

/* services */
.services{left:46px;top:326px;width:612px;height:156px;display:flex;border:1px solid var(--border);background:var(--card)}
.service{flex:1;text-align:center;border-right:1px solid var(--border);padding-top:28px;
  background:linear-gradient(#fafafa,#efefef)}
.service:last-child{border-right:none}
.service svg{display:block;margin:0 auto}
.service h3{font-family:"Roboto",Arial,sans-serif;font-weight:400;font-size:11.5px;color:var(--navy);margin-top:8px;letter-spacing:.2px}
.service p{font-size:9.2px;line-height:14.5px;margin:4px auto 0;width:160px}

/* welcome */
.welcome{left:0;top:508px;width:703px;text-align:center}
.welcome h2{font-family:"Roboto",Arial,sans-serif;font-weight:400;font-size:28px;color:var(--navy);letter-spacing:.3px}
.welcome h2 span{color:var(--orange)}
.tagline{position:relative;margin-top:3px;font-family:"Roboto",Arial,sans-serif;font-size:12px;color:var(--navy)}
.tagline::before,.tagline::after{content:"";position:absolute;top:9px;width:124px;height:1px;background:var(--navy)}
.tagline::before{left:123px}
.tagline::after{left:455px}
.welcome p{width:475px;margin:10px auto 0;font-size:9.2px;line-height:14.6px}

/* our work */
.work{left:0;top:654px;width:703px;height:213px;background:var(--light)}
.work h2{position:absolute;top:26px;width:100%;text-align:center;font-family:"Roboto",Arial,sans-serif;font-weight:400;font-size:25px;color:var(--navy);letter-spacing:.8px}
.client{position:absolute;top:80px;width:140px;margin-left:-70px;text-align:center}
.client-name{height:28px;line-height:28px;font-family:"Roboto",Arial,sans-serif;font-weight:700;font-size:15px;color:#333}
.client p{margin-top:11px;font-size:9.2px;line-height:16.8px}

/* tech strip */
.tech{left:0;top:867px;width:703px;height:131px}
.tech-name{position:absolute;top:56px;width:130px;margin-left:-65px;text-align:center;
  font-family:"Roboto",Arial,sans-serif;font-weight:700;font-size:20px;color:var(--grey-logo)}

/* footer */
.footer{left:0;top:998px;width:703px;height:202px;
  background:linear-gradient(90deg,#2c2a33 0%,#3b3640 45%,#4a4043 75%,#5a4a44 100%)}
.footer h4{position:absolute;top:31px;font-family:"Roboto",Arial,sans-serif;font-weight:400;font-size:11.5px;color:var(--white);letter-spacing:.3px}
.contact-item{position:absolute;left:46px;display:flex;gap:11px;font-size:9.2px;line-height:14px;color:var(--white)}
.contact-item svg{flex:none;margin-top:1px}
.field{position:absolute;left:257px;width:139px;height:22px;border:1px solid #d8d8d8;font-size:9px;color:#ddd;padding:5px 7px}
.subscribe{position:absolute;left:257px;top:120px;width:91px;height:28px;background:var(--white);color:var(--navy);
  font-family:"Roboto",Arial,sans-serif;font-size:9.5px;text-align:center;line-height:28px}
.links{position:absolute;left:452px;top:57px;list-style:none;font-family:"Roboto",Arial,sans-serif;font-size:9.5px;color:var(--white);line-height:18px}
.badge{position:absolute;top:51px;width:26px;height:42px}
.copyright{position:absolute;left:0;width:703px;top:170px;text-align:center;font-size:9.2px;color:var(--white)}
.copyright b{font-weight:700}
</style>
</head>
<body>

<div class="abs hero" role="img" aria-label="Photo of a woman in a hat holding a coffee cup while working at a laptop in a bright café"></div>

<header class="abs topbar"></header>
<div class="abs brand"><span class="brand-mark"></span>Kavreo</div>
<nav class="abs main-nav">
  <a class="active" href="#" style="left:0">HOME</a>
  <a href="#" style="left:60px">ABOUT US</a>
  <a href="#" style="left:140px">PORTFOLIO</a>
  <a href="#" style="left:223px">CONTACT US</a>
</nav>

<div class="abs hero-title">
  <div class="line1">GET STARTED WITH WORLD'S</div>
  <div class="line2">LEADING ECOMMERCE PLATFORM</div>
</div>

<section class="abs services">
  <div class="service">
    <svg width="50" height="34" viewBox="0 0 50 34" aria-hidden="true">
      <rect x="8" y="2" width="34" height="22" rx="2" fill="none" stroke="var(--orange)" stroke-width="3"/>
      <path d="M2 27h46v2a3 3 0 0 1-3 3H5a3 3 0 0 1-3-3z" fill="var(--orange)"/>
    </svg>
    <h3>DEVLOPMENT</h3>
    <p>We offer development, support and maintenance services to&nbsp; websites.</p>
  </div>
  <div class="service">
    <svg width="50" height="34" viewBox="0 0 50 34" aria-hidden="true">
      <rect x="1" y="8" width="7" height="20" fill="var(--orange)"/>
      <rect x="42" y="8" width="7" height="20" fill="var(--orange)"/>
      <path d="M10 10l10-4 8 3 6-3 6 4v14l-12 6-6-2-12-4z" fill="var(--orange)"/>
      <path d="M18 16l6 4M22 14l6 4" stroke="var(--white)" stroke-width="1.5"/>
    </svg>
    <h3>SUPPORT</h3>
    <p>We offer development, support and maintenance services to&nbsp; websites.</p>
  </div>
  <div class="service">
    <svg width="50" height="34" viewBox="0 0 50 34" aria-hidden="true">
      <path d="M13 4l24 26" stroke="var(--orange)" stroke-width="4" stroke-linecap="round"/>
      <circle cx="13" cy="6" r="5" fill="none" stroke="var(--orange)" stroke-width="2.5"/>
      <path d="M38 4l-22 24" stroke="var(--orange)" stroke-width="3" stroke-linecap="round"/>
      <path d="M14 26l-3 5" stroke="var(--orange)" stroke-width="5" stroke-linecap="round"/>
    </svg>
    <h3>MAINTENANCE</h3>
    <p>We offer development, support and maintenance services to&nbsp; websites.</p>
  </div>
</section>

<section class="abs welcome">
  <h2>WELCOME TO <span>KAVREO</span></h2>
  <div class="tagline">Leading eCommerce Platform</div>
  <p>We're a Melbourne based website development company. We specialise exclusively in Torvista e-commerce platform. What distinguishes our business from competition is that rather than designing and building brand new websites, we offer development, support and maintenance services to established websites. Maintenance and Support are the keywords representing our business.</p>
</section>

<section class="abs work">
  <h2>OUR WORK</h2>
  <div class="client" style="left:120px"><div class="client-name">Stockhaven</div>
    <p>Kavreo are great devlopers whise concentration on detail does not compromise</p></div>
  <div class="client" style="left:274px"><div class="client-name">Veloura</div>
    <p>In the lead-up to the now infamous Snap Rush of 2012, Australia's first landmark .</p></div>
  <div class="client" style="left:431px"><div class="client-name">Mirren</div>
    <p>Kavreo are great devlopers whise concentration on detail does not comprom&nbsp; .</p></div>
  <div class="client" style="left:586px"><div class="client-name">Lacefold</div>
    <p>After initial trial tasks, Bravuln conducted an inside out system audit of the Torvista .</p></div>
</section>

<section class="abs tech" aria-label="Technologies">
  <div class="tech-name" style="left:146px">Torvista</div>
  <div class="tech-name" style="left:263px">QRX</div>
  <div class="tech-name" style="left:399px">NCB</div>
  <div class="tech-name" style="left:546px">DataVane</div>
</section>

<footer class="abs footer" role="img" aria-label="Dim photo of a woman on the phone in a shop, behind the footer">
  <h4 style="left:46px">CONTACT</h4>
  <div class="contact-item" style="top:59px">
    <svg width="10" height="13" viewBox="0 0 10 13" aria-hidden="true"><path d="M5 0a5 5 0 0 1 5 5c0 3-5 8-5 8S0 8 0 5a5 5 0 0 1 5-5z" fill="#fff"/><circle cx="5" cy="5" r="2" fill="#3b3640"/></svg>
    <span>Suite 42, Level 3|8 Wattlebrook Lane<br>|Fernvale Heights VIC 3999</span>
  </div>
  <div class="contact-item" style="top:99px">
    <svg width="12" height="10" viewBox="0 0 12 10" aria-hidden="true"><rect x=".6" y=".6" width="10.8" height="8.8" fill="none" stroke="#fff" stroke-width="1.2"/><path d="M1 1l5 4 5-4" fill="none" stroke="#fff" stroke-width="1.2"/></svg>
    <span>support@kavreo.example</span>
  </div>
  <div class="contact-item" style="top:125px">
    <svg width="12" height="12" viewBox="0 0 12 12" aria-hidden="true"><path d="M2 0l3 3-1.5 2a8 8 0 0 0 3.5 3.5L9 7l3 3-2 2C5 12 0 7 0 2z" fill="#fff"/></svg>
    <span>1300 648 907</span>
  </div>

  <h4 style="left:257px">NEWSLETTER</h4>
  <div class="field" style="top:60px">Name</div>
  <div class="field" style="top:89px">Email</div>
  <div class="subscribe">SUBSCRIBE</div>

  <h4 style="left:452px;top:30px">USEFULL LINKS</h4>
  <ul class="links"><li>HOME</li><li>ABOUT</li><li>PORTFOLIO</li><li>CONTACT</li></ul>

  <h4 style="left:594px;top:30px">PARTNERS</h4>
  <div class="badge" style="left:596px;background:#f2f2f2"></div>
  <div class="badge" style="left:632px;background:var(--orange)"></div>

  <div class="copyright"><b>@ KAVREO ECOMMERCE</b>&nbsp; 2016 | All Rights Reserved</div>
</footer>

</body>
</html>
```